Product Packaging design for Vaporizer Battery box

We are looking for product packaging for a new line of Vaporizer Batteries. These batteries are all sold in bundle packs, and each battery has its own cardboard box. For example, the bundle packs are simply bagged up packs of 2, 3, 5, 10, 25, etc.

There are 4 different kinds of batteries that we need the packaging designed for. I have attached templates of the packaging for your reference. I would like the packaging to be a similar theme across all the batteries to keep things consistent.

More details about the 4 batteries can be found on our website at:
http://www.tidemarkgoodsdepot.example/product-category/vape_batteries/
Password: tidevisit

Packing Requirements

The packaging should have our company logo somewhere on it. I have attached a few different variations/orientations of our logo for you to choose between.

The name of the battery
Tidemark Goods 1300mAh Variable Voltage Large Capacity Battery
Tidemark Goods 400mAh Slim Variable Voltage Battery
Tidemark Goods 280mAh Slim Automatic Buttonless Battery
Tidemark Goods 350mAh KOV Slim Battery

Company website www.TidemarkGoodsDepot.example

For the Tidemark Goods 350mAh KOV Slim Battery, have the product packaging color scheme be Black base with Gold wording/trim. This battery only comes in black and gold, so the packaging will match.

Make sure to use the proper packaging template for the batteries. There are only two templates and pretty much the only difference is the size. They both fold up to be a rectangle package.

Industry/Entity Type

Product

Colors

Designer to choose colors to be used in the design.

Requirements
Must have
• Packing Requirements
• The packaging should have our company logo somewhere on it. I have attached a few different variations/orientations of our logo for you to choose between.
• The name of the battery
• Tidemark Goods 1300mAh Variable Voltage Large Capacity Battery
• Tidemark Goods 400mAh Slim Variable Voltage Battery
• Tidemark Goods 280mAh Slim Automatic Buttonless Battery
• Tidemark Goods 350mAh KOV Slim Battery
• Company website www.TidemarkGoodsDepot.example
• For the Tidemark Goods 350mAh KOV Slim Battery, have the product packaging color scheme be Black base with Gold wording/trim. This battery only comes in black and gold, so the packaging will match.
• Make sure to use the proper packaging template for the batteries. There are only two templates and pretty much the only difference is the size. They both fold up to be a rectangle package.

```html
<!DOCTYPE html>
<html lang="en">
<head>
<meta charset="utf-8">
<title>Tidemark Goods – 1300mAh Battery Box Dielines</title>
<link href="https://fonts.googleapis.com/css2?family=Montserrat:wght@400;500&display=swap" rel="stylesheet">
<style>
  :root {
    --stage-light: #f7941d;
    --stage-dark: #b4520f;
    --box-black: #050505;
    --flap-black: #222123;
    --pattern-base: #232224;
    --fold-line: #3a3134;
    --trim-blue: #3a44a8;
    --trim-gold: #f7c818;
    --label-white: #ffffff;
  }
  html, body {
    margin: 0;
    width: 1200px;
    height: 900px;
    overflow: hidden;
  }
  body {
    background: radial-gradient(ellipse at 50% 50%, var(--stage-light) 0%, #f07a16 45%, var(--stage-dark) 100%);
    font-family: "Montserrat", sans-serif;
  }
  .dieline-sheet { display: block; width: 1200px; height: 900px; }
  .flap { fill: var(--flap-black); }
  .body-lower { fill: var(--box-black); }
  .pattern-field { fill: var(--pattern-base); }
  .fold { stroke: var(--fold-line); stroke-width: 0.8; fill: none; }
  .brand-name { font-family: "Montserrat", sans-serif; font-weight: 500; letter-spacing: 0.5px; text-anchor: middle; }
  .flap-label { font-size: 12px; }
  .panel-label { font-size: 28px; letter-spacing: 1px; }
  .spec-text { font-family: "Montserrat", sans-serif; font-weight: 400; font-size: 11.5px; text-anchor: middle; }
  .colour-option { font-family: "Montserrat", sans-serif; font-weight: 400; font-size: 11px; fill: var(--label-white); }
  .tick-box { fill: var(--label-white); }
  .mark-shape { fill: var(--label-white); }
  .box-blue .trim, .box-blue .accent-text { fill: var(--trim-blue); }
  .box-gold .trim, .box-gold .accent-text { fill: var(--trim-gold); }
</style>
</head>
<body>
<svg class="dieline-sheet" viewBox="0 0 1200 900" xmlns="http://www.w3.org/2000/svg">
  <defs>
    <g id="box-dieline">
      <path class="flap" d="M349.6 157.6 V38 Q349.6 16 371.6 16 H420.4 Q442.4 16 442.4 38 V157.6 Z"/>
      <line class="fold" x1="349.6" y1="65.6" x2="442.4" y2="65.6"/>
      <polygon class="flap" points="256,157.6 256,150 266,150 266,113.6 334,113.6 349.6,148 349.6,157.6"/>
      <polygon class="flap" points="442.4,157.6 442.4,148 458,113.6 524,113.6 524,150 534.4,157.6"/>
      <polygon class="flap" points="256,745.6 256,752 266,756 266,789.6 334,789.6 349.6,756 349.6,745.6"/>
      <polygon class="flap" points="442.4,745.6 442.4,756 458,789.6 524,789.6 524,756 534.4,752 534.4,745.6"/>
      <path class="flap" d="M534.4 745.6 V863.6 Q534.4 885.6 556.4 885.6 H606 Q628 885.6 628 863.6 V745.6 Z"/>
      <line class="fold" x1="534.4" y1="837.6" x2="628" y2="837.6"/>
      <rect class="pattern-field" x="256" y="157.6" width="372" height="395" role="img" aria-label="Fine dark geometric star pattern across the upper box panels"/>
      <rect class="body-lower" x="256" y="552" width="372" height="193.6"/>
      <line class="fold" x1="349.6" y1="157.6" x2="349.6" y2="546"/>
      <line class="fold" x1="442.4" y1="157.6" x2="442.4" y2="546"/>
      <line class="fold" x1="534.4" y1="157.6" x2="534.4" y2="546"/>
    </g>
  </defs>

  <g class="box box-blue">
    <use href="#box-dieline"/>
    <polygon class="trim" points="256,546.4 349.6,546.4 396,573 442.4,546.4 628,546.4 628,557.6 442.4,557.6 396,590 349.6,557.6 256,557.6"/>
    <text class="brand-name flap-label accent-text" x="396" y="106">Tidemark</text>
    <text class="brand-name flap-label accent-text" x="396" y="121">Goods</text>
    <text class="brand-name panel-label accent-text" transform="translate(386 325) rotate(90)">Tidemark Goods</text>
    <text class="spec-text accent-text" x="396" y="618">1300mAh</text>
    <text class="spec-text accent-text" x="396" y="631">VARIABLE</text>
    <text class="spec-text accent-text" x="396" y="644">VOLTAGE</text>
    <text class="spec-text accent-text" x="396" y="670">LARGE</text>
    <text class="spec-text accent-text" x="396" y="683">CAPACITY</text>
    <text class="spec-text accent-text" x="396" y="696">BATTERY</text>
    <g class="colour-list">
      <text class="colour-option" transform="translate(467 648) rotate(-90)">GREEN</text>
      <text class="colour-option" transform="translate(482 648) rotate(-90)">PURPLE</text>
      <text class="colour-option" transform="translate(497 648) rotate(-90)">STAINLESS</text>
      <text class="colour-option" transform="translate(512 648) rotate(-90)">TITANIUM</text>
      <text class="colour-option" transform="translate(467 709) rotate(-90)">BLACK</text>
      <text class="colour-option" transform="translate(482 709) rotate(-90)">WHITE</text>
      <text class="colour-option" transform="translate(497 709) rotate(-90)">RED</text>
      <text class="colour-option" transform="translate(512 709) rotate(-90)">BLUE</text>
      <rect class="tick-box" x="458" y="655" width="10" height="10"/>
      <rect class="tick-box" x="473" y="655" width="10" height="10"/>
      <rect class="tick-box" x="488" y="655" width="10" height="10"/>
      <rect class="tick-box" x="503" y="655" width="10" height="10"/>
      <rect class="tick-box" x="458" y="716" width="10" height="10"/>
      <rect class="tick-box" x="473" y="716" width="10" height="10"/>
      <rect class="tick-box" x="488" y="716" width="10" height="10"/>
      <rect class="tick-box" x="503" y="716" width="10" height="10"/>
    </g>
    <g class="compliance-marks">
      <rect class="mark-shape" x="572" y="587" width="22" height="20" rx="3"/>
      <circle class="mark-shape" cx="583" cy="637" r="13"/>
      <circle class="mark-shape" cx="583" cy="678" r="11"/>
      <rect class="mark-shape" x="565" y="700" width="34" height="22" rx="2"/>
    </g>
    <text class="brand-name flap-label accent-text" x="581" y="786">Tidemark</text>
    <text class="brand-name flap-label accent-text" x="581" y="801">Goods</text>
  </g>

  <g class="box box-gold" transform="translate(398.4 0)">
    <use href="#box-dieline"/>
    <polygon class="trim" points="256,546.4 349.6,546.4 396,573 442.4,546.4 628,546.4 628,557.6 442.4,557.6 396,590 349.6,557.6 256,557.6"/>
    <text class="brand-name flap-label accent-text" x="396" y="106">Tidemark</text>
    <text class="brand-name flap-label accent-text" x="396" y="121">Goods</text>
    <text class="brand-name panel-label accent-text" transform="translate(386 325) rotate(90)">Tidemark Goods</text>
    <text class="spec-text accent-text" x="396" y="618">1300mAh</text>
    <text class="spec-text accent-text" x="396" y="631">VARIABLE</text>
    <text class="spec-text accent-text" x="396" y="644">VOLTAGE</text>
    <text class="spec-text accent-text" x="396" y="670">LARGE</text>
    <text class="spec-text accent-text" x="396" y="683">CAPACITY</text>
    <text class="spec-text accent-text" x="396" y="696">BATTERY</text>
    <g class="colour-list">
      <text class="colour-option" transform="translate(467 648) rotate(-90)">GREEN</text>
      <text class="colour-option" transform="translate(482 648) rotate(-90)">PURPLE</text>
      <text class="colour-option" transform="translate(497 648) rotate(-90)">STAINLESS</text>
      <text class="colour-option" transform="translate(512 648) rotate(-90)">TITANIUM</text>
      <text class="colour-option" transform="translate(467 709) rotate(-90)">BLACK</text>
      <text class="colour-option" transform="translate(482 709) rotate(-90)">WHITE</text>
      <text class="colour-option" transform="translate(497 709) rotate(-90)">RED</text>
      <text class="colour-option" transform="translate(512 709) rotate(-90)">BLUE</text>
      <rect class="tick-box" x="458" y="655" width="10" height="10"/>
      <rect class="tick-box" x="473" y="655" width="10" height="10"/>
      <rect class="tick-box" x="488" y="655" width="10" height="10"/>
      <rect class="tick-box" x="503" y="655" width="10" height="10"/>
      <rect class="tick-box" x="458" y="716" width="10" height="10"/>
      <rect class="tick-box" x="473" y="716" width="10" height="10"/>
      <rect class="tick-box" x="488" y="716" width="10" height="10"/>
      <rect class="tick-box" x="503" y="716" width="10" height="10"/>
    </g>
    <g class="compliance-marks">
      <rect class="mark-shape" x="572" y="587" width="22" height="20" rx="3"/>
      <circle class="mark-shape" cx="583" cy="637" r="13"/>
      <circle class="mark-shape" cx="583" cy="678" r="11"/>
      <rect class="mark-shape" x="565" y="700" width="34" height="22" rx="2"/>
    </g>
    <text class="brand-name flap-label accent-text" x="581" y="786">Tidemark</text>
    <text class="brand-name flap-label accent-text" x="581" y="801">Goods</text>
  </g>
</svg>
</body>
</html>
```